KVR Inc Web Design

WHAT ARE WE DOING?
We are developing a new website look and feel for a new company called KVR Inc. This new look and feel should include colors, design elements, choice of photography and other imagery, fonts, and other user experience elements.

WHAT DO THEY DO?
KVR, Inc, makes tools for researchers who are studying protein-protein interactions. These molecules are the basic tools of biology, and serve as key targets for drug developers and disease researchers. The world of proteins is enormously complex, and companies like KVR provide researchers with critical tools that help them elucidate this world.

WHO ARE WE TALKING TO?
The target audience for this website are professional scientists working in university research or biopharma drug development. They are highly sophisticated consumers looking for key tools that will advance their research.

WHAT DO WE WANT THEM TO DO?
The site is an information resource for the customer exploring the tools that KVR sells and the scientific issues surrounding protein-protein interactions. They should be able to navigate easily to their content of choice, while the whole site should convey a professionalism that enhanced KVR’s credibility.

WHAT DOES THE KVR BRAND STAND FOR?
KVR stands for illumination. Proteins are challenging to study, and KVR exists to help shed light on their workings.

WHAT ARE THE KEY VALUES OF THE KVR BRAND?
Integrity. Innovation. Insight.

WHAT ARE THE EXECUTIONAL MANDITORIES?
The look and feel is completely up for grabs. Nothing is off the table.

WHAT ARE THE DELIVERABLES?
We need new designs for the following templates:
http://cms.marlowbench.com/
http://cms.marlowbench.com/products-and-services/instruments-3/bench-top-instruments/
http://cms.marlowbench.com/category/lab-study/

```html
<!DOCTYPE html>
<html lang="en">
<head>
<meta charset="utf-8">
<title>KVR Inc</title>
<link href="https://fonts.googleapis.com/css2?family=Source+Sans+3:wght@400;600;700&family=Roboto+Condensed:wght@500;700&display=swap" rel="stylesheet">
<style>
:root{
  --bar:#8c8c8c;
  --bar-field:#a3a3a3;
  --ink:#4a4a4a;
  --muted:#6b6b6b;
  --orange:#f2a024;
  --panel:#f0f0f0;
  --icon:#555555;
  --white:#ffffff;
  --button:#525252;
  --logo-box:#d8d8d8;
}
*{margin:0;padding:0;box-sizing:border-box}
html,body{width:1200px;height:850px;overflow:hidden;background:var(--white)}
body{font-family:"Source Sans 3",sans-serif;color:var(--ink);position:relative}
a{color:inherit;text-decoration:none}

.topbar{position:absolute;left:0;top:0;width:1200px;height:49px;background:var(--bar);color:var(--white)}
.search{position:absolute;left:386px;top:13px;width:201px;height:23px;background:var(--bar-field);border-radius:2px;font-size:8px;line-height:23px;padding-left:10px;letter-spacing:.3px}
.search svg{position:absolute;right:9px;top:5px}
.phone{position:absolute;left:614px;top:14px;font-size:13px;display:flex;align-items:center;gap:6px}
.toplinks{position:absolute;left:718px;top:18px;font-size:9.5px;font-weight:600;display:flex;gap:12px}
.social{position:absolute;top:12px;width:24px;height:24px;border-radius:50%;background:#7a7a7a}

.logo{position:absolute;left:180px;top:70px;height:34px;display:flex;align-items:center;gap:10px}
.logo .box{width:28px;height:28px;background:var(--logo-box)}
.logo .name{font-size:30px;font-weight:600;color:var(--ink);line-height:1}
.mainnav{position:absolute;right:181px;top:93px;display:flex;gap:44px;font-size:9.5px;color:var(--muted);text-transform:uppercase}

.hero{position:absolute;left:180px;top:121px;width:840px;height:274px;background:linear-gradient(100deg,#cfd8e2 0%,#aebccb 35%,#dcdfe3 60%,#c9ced4 100%)}
.hero-title{position:absolute;right:33px;top:196px;text-align:right;font-family:"Roboto Condensed",sans-serif;color:#1f1f1f;text-transform:uppercase}
.hero-title .l1{font-size:26px;font-weight:500;line-height:1}
.hero-title .l2{font-size:16.5px;font-weight:700;margin-top:9px;line-height:1}
.hero-dots{position:absolute;right:13px;top:253px;display:flex;gap:6px}
.hero-dots span{width:12px;height:12px;border-radius:50%;border:1px solid var(--white);background:rgba(255,255,255,.35)}

.features{position:absolute;left:180px;top:417px;width:840px;height:166px;display:flex;gap:7px}
.feature{flex:1;background:var(--panel);text-align:center;padding-top:14px;color:var(--muted)}
.feature .icon{width:43px;height:43px;border-radius:50%;background:var(--icon);margin:0 auto;display:flex;align-items:center;justify-content:center}
.feature h3{font-size:14.5px;font-weight:600;color:var(--ink);margin-top:9px;text-transform:uppercase;letter-spacing:.2px}
.feature p{font-size:9px;line-height:15.5px;margin:6px 24px 0}
.feature.active{background:var(--orange);color:var(--white)}
.feature.active h3{color:var(--white)}
.feature.active .icon{background:#d9861a}

.section-title{position:absolute;left:180px;top:614px;font-size:14.5px;font-weight:700;color:var(--ink);text-transform:uppercase}
.instrument-photo{position:absolute;left:180px;top:647px;width:245px;height:137px;border:3px solid #ececec;background:linear-gradient(160deg,#b9c9dc 0%,#e7ecf3 55%,#9aacc0 100%)}
.intro{position:absolute;left:444px;top:649px;width:566px;font-size:9.2px;line-height:15.5px;color:var(--muted)}
.intro p+p{margin-top:15.5px}
.cta{position:absolute;left:446px;top:753px;width:156px;height:31px;background:var(--button);color:var(--white);border-radius:3px;font-size:10.5px;font-weight:700;text-align:center;line-height:31px;text-transform:uppercase}

.footer{position:absolute;left:0;top:812px;width:1200px;height:38px;background:var(--bar);color:var(--white);font-size:9.5px;font-weight:600}
.footer nav{position:absolute;left:182px;top:13px;display:flex;gap:13px}
.footer .copy{position:absolute;right:180px;top:13px}
</style>
</head>
<body>

<header class="topbar">
  <div class="search">SEARCH :
    <svg width="14" height="13" viewBox="0 0 14 13"><circle cx="5.5" cy="5.5" r="4" fill="none" stroke="#e2e2e2" stroke-width="1.6"/><line x1="8.5" y1="8.5" x2="12.5" y2="12" stroke="#e2e2e2" stroke-width="2"/></svg>
  </div>
  <div class="phone">
    <svg width="18" height="18" viewBox="0 0 18 18"><path d="M4 1c1 0 2 3 2 4s-2 1-1 3 3 4 4 4 1-2 2-2 4 1 4 2-2 4-4 4C7 16 2 10 2 5c0-2 1-4 2-4z" fill="#fff"/></svg>
    05180-3344
  </div>
  <nav class="toplinks">
    <a href="#">Home</a><span>|</span>
    <a href="#">Our Clients</a><span>|</span>
    <a href="#">Contact Us</a><span>|</span>
    <a href="#">Sitemap</a>
  </nav>
  <span class="social" style="left:962px"></span>
  <span class="social" style="left:992px"></span>
</header>

<div class="logo"><span class="box"></span><span class="name">KVR Inc</span></div>

<nav class="mainnav">
  <a href="#">Company</a>
  <a href="#">Products &amp; Services</a>
  <a href="#">Learning Center</a>
  <a href="#">Events</a>
  <a href="#">KVR News</a>
  <a href="#">Contact Us</a>
</nav>

<section class="hero" role="img" aria-label="Photo of two scientists in a laboratory examining a flask">
  <div class="hero-title">
    <div class="l1">KVR, Inc, makes tools</div>
    <div class="l2">for researchers who are studying protein-protein interactions</div>
  </div>
  <div class="hero-dots"><span></span><span></span></div>
</section>

<section class="features">
  <article class="feature active">
    <div class="icon"><svg width="24" height="22" viewBox="0 0 24 22"><circle cx="13" cy="5" r="3" fill="#fff"/><path d="M2 13h6l3 2h6l5-3v3l-5 4H6l-4-2z" fill="#fff"/></svg></div>
    <h3>Innovation</h3>
    <p>Lorem ipsum dolor sit amet, consectetur adipiscing elit. Proin placerat nulla massa, a condimentum leo tincidunt vel.Consectetur adipiscing elit. Proin placerat nulla massa, a condimentum leo.</p>
  </article>
  <article class="feature">
    <div class="icon"><svg width="24" height="22" viewBox="0 0 24 22"><circle cx="8" cy="14" r="5" fill="none" stroke="#fff" stroke-width="3" stroke-dasharray="2.5 1.5"/><circle cx="17" cy="6" r="3.5" fill="none" stroke="#fff" stroke-width="2.5" stroke-dasharray="2 1.3"/></svg></div>
    <h3>Automation</h3>
    <p>Lorem ipsum dolor sit amet, consectetur adipiscing elit. Proin placerat nulla massa, a condimentum leo tincidunt vel.Consectetur adipiscing elit. Proin placerat nulla massa, a condimentum leo.</p>
  </article>
  <article class="feature">
    <div class="icon"><svg width="24" height="22" viewBox="0 0 24 22"><circle cx="8" cy="8" r="5" fill="none" stroke="#fff" stroke-width="2.6"/><line x1="12" y1="12" x2="20" y2="18" stroke="#fff" stroke-width="3.5" stroke-linecap="round"/></svg></div>
    <h3>Research</h3>
    <p>Lorem ipsum dolor sit amet, consectetur adipiscing elit. Proin placerat nulla massa, a condimentum leo tincidunt vel.Consectetur adipiscing elit. Proin placerat nulla massa, a condimentum leo.</p>
  </article>
</section>

<h2 class="section-title">Bench Top Instruments</h2>
<div class="instrument-photo" role="img" aria-label="Photo of an automated bench top laboratory instrument"></div>
<div class="intro">
  <p>Maecenas imperdiet nisi eu justo dapibus, commodo venenatis massa tempus. Morbi consectetur sed justo vitae dictum. Ut semper tincidunt accumsan.Nunc suscipit dui in massa ultricies, ac sagittis velit pulvinar. In scelerisque id lectus eu facilisis. Morbi et nunc non nulla lobortis ultricies sit amet a turpis. Integer eget ullamcorper metus.</p>
  <p>Cras vitae nibh non dolor scelerisque porta.Nunc suscipit dui in massa ultricies, ac sagittis velit pulvinar. In scelerisque id lectus eu facilisis. Morbi et nunc non nulla lobortis ultricies sit amet a turpis. Integer eget ullamcorper metus.</p>
</div>
<a class="cta" href="#">View our instruments</a>

<footer class="footer">
  <nav>
    <a href="#">Home</a><span>|</span>
    <a href="#">Company</a><span>|</span>
    <a href="#">Products &amp; Services</a><span>|</span>
    <a href="#">Contact Us</a><span>|</span>
    <a href="#">Site Map</a><span>|</span>
    <a href="#">Privacy Policy</a><span>|</span>
    <a href="#">Terms</a>
  </nav>
  <div class="copy">Copyright. 2013. kvrinc. All rights reserved.</div>
</footer>

</body>
</html>
```